Delia Marsh Catalog to submit to vendors

We need a catalog made with all of the products in our shop for sales purposes. Our Website is www.deliamarshandcompany.example
Almost all of our products are listed on the website. If you can not take the pictures from the site I can upload them. The descriptions are listed as well. There are three additional products that I will upload. This Catalog will be mailed to stores and should include MSRP Prices.
Updates

Hello There-We are looking for a sales catalog to send to stores in our area. We would like to include MSRP and the end we can add wholesale pricing with minimum orders. Our website is www.deliamarshandcompany.example. There are a few products that haven't been added to the website yet. Where can I upload them and send descriptions?Thank you,Colette Added Thursday, January 21, 2016

Target Market(s)

boutiques and gift shops

Industry/Entity Type

Shop

Font styles to use
Serif
Other font styles liked:
• Noteworthy

Colors
e34297
a64599
6b449b
0255a3

Requirements
Must have
• Color! I would like to organize the catalog by sections. Our premade section and our DIY kits. Maybe we should include Gift sets and put the baskets and gift boxes in one section

```html
<!DOCTYPE html>
<html lang="en">
<head>
<meta charset="utf-8">
<title>Delia Marsh Catalog – Pages 3 and 4</title>
<link rel="stylesheet" href="https://fonts.googleapis.com/css2?family=Patrick+Hand&family=Kalam:wght@700&display=swap">
<style>
  :root {
    --pink: #e34297;
    --orchid: #a64599;
    --purple: #6b449b;
    --price: #4c2d8c;
    --blue: #0255a3;
    --paper: #ffffff;
    --backdrop: #ececf1;
  }
  * { box-sizing: border-box; margin: 0; padding: 0; }
  html, body { width: 1200px; height: 1000px; overflow: hidden; }
  body { background: var(--backdrop); position: relative; font-family: "Patrick Hand", cursive; }

  .spread {
    position: absolute; left: 12px; top: 208px; width: 1174px; height: 414px;
    background: var(--paper);
    box-shadow: 0 3px 8px rgba(0,0,0,.35);
  }
  .page-band { position: absolute; bottom: 2px; height: 22px; }
  .page-band--diy { left: 0; width: 587px; background: var(--blue); }
  .page-band--premade { left: 587px; width: 587px; background: var(--pink); }

  .section-title {
    position: absolute; height: 50px; border-radius: 26px;
    color: #fff; font-family: "Kalam", cursive; font-weight: 700;
    font-size: 36px; line-height: 54px; text-align: center;
  }
  .section-title--diy { left: 42px; top: 220px; width: 546px; background: var(--blue); }
  .section-title--premade { left: 628px; top: 220px; width: 544px; background: var(--pink); }
  .section-title .tail { position: absolute; right: -14px; bottom: -10px; width: 40px; height: 24px; }
  .page-number {
    position: absolute; top: 0; font-family: "Patrick Hand", sans-serif;
    font-size: 20px; font-weight: 400; line-height: 50px;
  }
  .section-title--diy .page-number { left: 14px; }
  .section-title--premade .page-number { right: 10px; }

  .photo {
    position: absolute; border-radius: 16px; border: 7px solid var(--blue);
  }
  .photo--pink { border-color: var(--pink); border-width: 6px; }
  .photo--lipbalm { left: 52px; top: 281px; width: 141px; height: 111px; background: linear-gradient(135deg, #e27ab7, #f6d3e6 55%, #c76aa8); }
  .photo--meteor { left: 237px; top: 290px; width: 141px; height: 111px; background: linear-gradient(135deg, #3f5bc4, #c9d3f1 50%, #5a78d4); }
  .photo--scrub { left: 422px; top: 281px; width: 141px; height: 111px; background: linear-gradient(135deg, #d267ad, #f2dcea 55%, #c8559e); }
  .photo--party { left: 136px; top: 438px; width: 141px; height: 111px; background: linear-gradient(135deg, #d86ab0, #f3e5ee 50%, #c65aa2); }
  .photo--bathkit { left: 343px; top: 438px; width: 141px; height: 111px; background: linear-gradient(135deg, #d970b4, #f0e4ee 50%, #cf5ea7); }
  .photo--spa { left: 636px; top: 283px; width: 167px; height: 126px; background: linear-gradient(135deg, #f2cdb8, #f7e3ea 45%, #b9dcd6); }
  .photo--assorted { left: 781px; top: 345px; width: 168px; height: 126px; background: radial-gradient(circle at 50% 55%, #c72d8c, #9e1472); }
  .photo--special { left: 981px; top: 283px; width: 169px; height: 126px; background: linear-gradient(160deg, #f3ece8, #9fd8dc 50%, #efe6df); }
  .photo--cupcake { left: 858px; top: 458px; width: 169px; height: 126px; background: linear-gradient(90deg, #9a64c4, #e85aa6 50%, #36b8c4); }

  .product { position: absolute; text-align: center; transform: translateX(-50%); white-space: nowrap; }
  .product__name { color: var(--pink); font-size: 17px; line-height: 20px; }
  .product__price { color: var(--price); font-size: 21px; line-height: 22px; }
</style>
</head>
<body>
  <main class="spread" aria-label="Catalog spread"></main>
  <div class="page-band page-band--diy"></div>
  <div class="page-band page-band--premade"></div>

  <h2 class="section-title section-title--diy">
    <span class="page-number">3</span>Do It Yourself Kit
    <svg class="tail" viewBox="0 0 40 24"><path d="M0 0 L40 24 L22 0 Z" fill="#0255a3"/></svg>
  </h2>
  <h2 class="section-title section-title--premade">
    Pre-Made Collection<span class="page-number">4</span>
    <svg class="tail" viewBox="0 0 40 24"><path d="M0 0 L40 24 L22 0 Z" fill="#e34297"/></svg>
  </h2>

  <div class="photo photo--lipbalm" role="img" aria-label="Lip balm kit contents on a pink backdrop"></div>
  <div class="product" style="left:124px;top:394px"><p class="product__name">Lip Balm Kit</p><p class="product__price">from $28.00</p></div>

  <div class="photo photo--meteor" role="img" aria-label="Meteor bath rox kit supplies on a blue backdrop"></div>
  <div class="product" style="left:308px;top:405px"><p class="product__name">Meteor Bath Rox Kit</p><p class="product__price">$16.00</p></div>

  <div class="photo photo--scrub" role="img" aria-label="Body scrub kit with glass stand and bottle"></div>
  <div class="product" style="left:493px;top:394px"><p class="product__name">Single Body Scrub Kit</p><p class="product__price">from $18.00</p></div>

  <div class="photo photo--party" role="img" aria-label="Party kit with jars, colorants and supplies"></div>
  <div class="product" style="left:208px;top:551px"><p class="product__name">Party Kit</p><p class="product__price">$99.00</p></div>

  <div class="photo photo--bathkit" role="img" aria-label="Bath bomb kit with bowl and colored powders"></div>
  <div class="product" style="left:413px;top:551px"><p class="product__name">Bath Bomb Kit</p><p class="product__price">$16.00</p></div>

  <div class="photo photo--pink photo--spa" role="img" aria-label="Pastel spa bath bombs"></div>
  <div class="product" style="left:719px;top:413px"><p class="product__name">Spa Bath Bombs<br>Collection</p><p class="product__price">$6.00</p></div>

  <div class="photo photo--pink photo--assorted" role="img" aria-label="Flower shaped bath bombs on pink glitter"></div>
  <div class="product" style="left:800px;top:475px"><p class="product__name">Assorted<br>Bath Bombs</p><p class="product__price">from $5.00</p></div>

  <div class="photo photo--pink photo--special" role="img" aria-label="Ice cream cone bath bombs"></div>
  <div class="product" style="left:1074px;top:414px"><p class="product__name">Special Edition<br>Bath Bombs</p><p class="product__price">$9.00</p></div>

  <div class="photo photo--pink photo--cupcake" role="img" aria-label="Soap and bath bomb cupcakes in purple, pink and teal"></div>
  <div class="product" style="left:1100px;top:507px"><p class="product__name" style="line-height:17px">Soap &amp; Bath Bomb<br>Cupcake Combo<br>(Multi-Color)</p><p class="product__price">$from 6.00</p></div>
</body>
</html>
```